Business Card Design

Hi I need a business card designed, we already have the business name logo artwork and would like some concept ideas for the Bus Card layout.
On the back of the card i want to include the products and services that we offer.
We are a Plastics Sheeting manufacture based in Perth Australia.

                                       

We need a BC design for a company called Tarvo Plastics based in Perth Australia.

We supply from DIY to Trade & Industrial  Engineering Markets.

We specialise in:

·         Cut to size panels  (all shapes and sizes)

·         Plastics fabrication & Welding

·         Custom Designs

·         Plastic Repairs

·         PVC Pipe Slotting & PVC Pipe Threading

·         Supplier of all types of engineering plastics and profiles.

Including:           Acrylic / Clarvene

                               Polycarbonate / Dorvil

                               Prismatic Light Diffuser

                               Vantrib

                               HDPE / UHMWPE

                               PVC / PVC Foam

                               Nylon

                               HIPS

```html
<!DOCTYPE html>
<html lang="en">
<head>
<meta charset="utf-8">
<title>Tarvo Plastics – Business Card</title>
<link href="https://fonts.googleapis.com/css2?family=Open+Sans:wght@400;600;700;800&display=swap" rel="stylesheet">
<style>
  :root {
    --navy: #0d2a63;
    --orange: #e07a1c;
    --gold: #e6a915;
    --white: #ffffff;
    --ink: #333a44;
    --backdrop: #e9ebef;
  }
  * { box-sizing: border-box; margin: 0; padding: 0; }
  html, body { width: 1200px; height: 987px; overflow: hidden; }
  body {
    background: var(--backdrop);
    font-family: "Open Sans", Arial, sans-serif;
    position: relative;
  }
  .card {
    position: absolute;
    width: 640px;
    height: 390px;
    border-radius: 26px;
    overflow: hidden;
    box-shadow: 0 10px 30px rgba(0,0,0,0.18);
  }

  /* Front */
  .card-front { left: 50px; top: 540px; background: var(--white); }
  .front-swoosh { position: absolute; inset: 0; }
  .brand-name {
    position: absolute;
    left: 150px; top: 40px;
    font-weight: 800;
    font-size: 60px;
    color: var(--navy);
    letter-spacing: -1px;
  }
  .holder { position: absolute; left: 40px; top: 130px; }
  .holder-name { font-weight: 700; font-size: 20px; color: var(--navy); }
  .holder-title { font-weight: 400; color: var(--orange); }
  .holder-address { margin-top: 6px; font-size: 15px; line-height: 21px; color: var(--ink); }
  .contact {
    position: absolute;
    right: 32px; top: 240px;
    text-align: right;
    color: var(--white);
    font-size: 14.5px;
    line-height: 21px;
  }
  .contact-line { display: flex; justify-content: flex-end; align-items: center; gap: 6px; }
  .contact-line svg { width: 13px; height: 13px; }

  /* Back */
  .card-back { left: 510px; top: 70px; background: var(--gold); padding: 28px 34px; text-align: center; }
  .back-brand { font-weight: 800; font-size: 44px; color: var(--navy); letter-spacing: -1px; }
  .back-tagline {
    margin-top: 6px;
    font-weight: 700; font-size: 15px; line-height: 19px;
    color: var(--white);
  }
  .back-heading { margin-top: 10px; font-weight: 700; font-size: 18px; color: var(--navy); }
  .back-list { font-size: 13.5px; line-height: 19px; color: var(--navy); }
</style>
</head>
<body>

<section class="card card-front" aria-label="Business card front">
  <svg class="front-swoosh" viewBox="0 0 640 390" preserveAspectRatio="none" aria-hidden="true">
    <path d="M0 190 C 110 300, 360 320, 580 250 L580 262 C 360 345, 100 330, 0 250 Z" fill="var(--orange)"/>
    <path d="M0 250 C 150 340, 420 300, 640 150 L640 390 L0 390 Z" fill="var(--navy)" stroke="var(--white)" stroke-width="8"/>
  </svg>

  <div class="brand-name">Tarvo Plastics</div>

  <div class="holder">
    <p class="holder-name">Your Name, <span class="holder-title">Title</span></p>
    <p class="holder-address">Unit 4/18 Marlow Crescent<br>Kelmscott Park WA 6150</p>
  </div>

  <div class="contact">
    <p class="contact-line">
      <svg viewBox="0 0 16 16" aria-hidden="true"><circle cx="8" cy="8" r="7" fill="none" stroke="#fff" stroke-width="1.5"/><path d="M5 5 Q6 11 11 11" stroke="#fff" stroke-width="2" fill="none"/></svg>
      08 9400 3170</p>
    <p class="contact-line">
      <svg viewBox="0 0 16 16" aria-hidden="true"><rect x="4" y="1" width="8" height="14" rx="1.5" fill="#fff"/><rect x="5.5" y="3" width="5" height="6" fill="var(--navy)"/></svg>
      123-456-7890</p>
    <p class="contact-line">
      <svg viewBox="0 0 16 16" aria-hidden="true"><rect x="1" y="6" width="14" height="8" rx="1" fill="#fff"/><rect x="4" y="2" width="8" height="5" fill="#fff"/></svg>
      08 9400 3171</p>
    <p class="contact-line">
      <svg viewBox="0 0 16 16" aria-hidden="true"><rect x="1" y="3" width="14" height="10" rx="1" fill="#fff"/><path d="M1 3 L8 9 L15 3" stroke="var(--navy)" stroke-width="1.3" fill="none"/></svg>
      sales@tarvoplastics.com.au</p>
    <p class="contact-line">PO Box 2284 Kelmscott Park DC WA 6972</p>
    <p class="contact-line">Brenlow Holdings Pty Ltd T/A Tarvo Plastics ABN: TBA</p>
  </div>
</section>

<section class="card card-back" aria-label="Business card back">
  <div class="back-brand">Tarvo Plastics</div>
  <p class="back-tagline">The Products And Services That We Offer<br>Are Supplied From DIY To Trade &amp; Industrial Engineering Markets</p>
  <p class="back-heading">We specialise in:</p>
  <p class="back-list">
    • Cut to size panels (all shapes and sizes) • Plastics fabrication &amp; Welding<br>
    • Custom Designs • Plastic Repairs • PVC Pipe Slotting &amp; PVC Pipe Threading<br>
    • Supplier of all types of engineering plastics and profiles
  </p>
  <p class="back-heading">Including:</p>
  <p class="back-list">
    • Acrylic / Clarvene • Polycarbonate / Dorvil • Prismatic Light Diffuser • Vantrib<br>
    • HDPE / UHMWPE • PVC / PVC Foam • Nylon • HIPS
  </p>
</section>

</body>
</html>
```